Redesign of business card for Cedar Ridge Mechanical

We are looking for a new design for our business cards for Cedar Ridge Mechanical. We are a plumbing & HVAC construction company, operating on the West Coast of Canada and USA. Logo attached.
Industry/Entity Type
Construction - Plumbing & HVAC
Contact Information for Business Card
Name, address, phone numbers, email, website address
Look and feel
Each slider illustrates characteristics of the customer's brand and the style your logo design should communicate.

```html
<!DOCTYPE html>
<html lang="en">
<head>
<meta charset="utf-8">
<title>Cedar Ridge Mechanical – Business Card</title>
<link href="https://fonts.googleapis.com/css2?family=Montserrat:wght@400;500;700&display=swap" rel="stylesheet">
<style>
  :root {
    --stage: #1c1c1c;
    --card-dark: #1e1e1e;
    --card-light: #ffffff;
    --swoosh: #8c8c8c;
    --ink: #141414;
    --ink-muted: #6e6e6e;
    --logo-text: #ffffff;
  }
  html, body {
    margin: 0;
    width: 1200px;
    height: 963px;
    overflow: hidden;
    background: var(--stage);
    font-family: "Montserrat", sans-serif;
  }
  .business-card {
    position: absolute;
    left: 180px;
    top: 241px;
    width: 840px;
    height: 480px;
    border-radius: 28px;
    overflow: hidden;
    background: var(--card-light);
    box-shadow: 0 20px 50px rgba(0,0,0,0.55);
  }
  .card-waves {
    position: absolute;
    inset: 0;
  }
  .brand {
    position: absolute;
    left: 60px;
    top: 62px;
    display: flex;
    align-items: center;
    gap: 18px;
    color: var(--logo-text);
    font-weight: 700;
    font-size: 30px;
    letter-spacing: 1px;
    text-transform: uppercase;
    line-height: 1.15;
  }
  .brand-square {
    width: 64px;
    height: 64px;
    border: 5px solid var(--logo-text);
    border-radius: 8px;
    box-sizing: border-box;
    flex: none;
  }
  .address {
    position: absolute;
    left: 60px;
    top: 300px;
    color: var(--ink-muted);
    font-size: 20px;
    line-height: 1.25;
  }
  .contact-block {
    position: absolute;
    right: 56px;
    top: 305px;
    text-align: right;
  }
  .person-name {
    font-weight: 700;
    font-size: 30px;
    color: var(--ink);
    letter-spacing: 1px;
    margin: 0;
  }
  .person-name .surname { color: var(--ink-muted); }
  .person-role {
    color: var(--ink-muted);
    font-size: 20px;
    margin: 2px 0 14px;
  }
  .contact-line {
    display: flex;
    justify-content: flex-end;
    align-items: center;
    gap: 10px;
    font-size: 20px;
    color: var(--ink-muted);
    line-height: 1.3;
  }
  .contact-line strong { color: var(--ink); font-weight: 500; }
  .contact-icon { width: 18px; height: 18px; flex: none; }
</style>
</head>
<body>
  <div class="business-card">
    <svg class="card-waves" viewBox="0 0 840 480" width="840" height="480" aria-hidden="true">
      <path fill="var(--card-dark)" d="M0 0H840V270C760 262 690 292 560 296C400 300 300 228 160 214C90 207 40 205 0 208Z"/>
      <path fill="var(--swoosh)" d="M0 150C120 150 220 215 360 240C480 262 620 262 840 238V252C620 278 480 278 360 256C220 232 120 168 0 166Z"/>
      <path fill="none" stroke="var(--swoosh)" stroke-width="2" d="M150 218C260 240 360 262 500 266"/>
    </svg>

    <div class="brand">
      <span class="brand-square"></span>
      <span>Cedar Ridge<br>Mechanical</span>
    </div>

    <div class="address">Your address, city<br>state, ZIP 0000</div>

    <div class="contact-block">
      <p class="person-name">DANIEL <span class="surname">BROOKS</span></p>
      <p class="person-role">Manager</p>
      <div class="contact-line">123-456-2100
        <svg class="contact-icon" viewBox="0 0 20 20"><circle cx="10" cy="10" r="10" fill="var(--ink)"/><path d="M7 5l2 2-1 1.5c.7 1.5 1.8 2.6 3.3 3.3L12.8 11l2 2-1.3 1.5C9.5 14 6 10.5 5.5 6.5Z" fill="#fff"/></svg>
      </div>
      <div class="contact-line">youremail@mailbox.com
        <svg class="contact-icon" viewBox="0 0 20 20"><circle cx="10" cy="10" r="10" fill="var(--ink)"/><rect x="5" y="6.5" width="10" height="7" fill="#fff"/><path d="M5 6.5l5 4 5-4" fill="none" stroke="var(--ink)" stroke-width="1.2"/></svg>
      </div>
      <div class="contact-line"><span>www.<strong>yourwebsite</strong>.com</span>
        <svg class="contact-icon" viewBox="0 0 20 20"><circle cx="10" cy="10" r="10" fill="var(--ink)"/><circle cx="10" cy="10" r="5" fill="none" stroke="#fff" stroke-width="1.3"/><path d="M5 10h10M10 5c-2.5 3-2.5 7 0 10M10 5c2.5 3 2.5 7 0 10" fill="none" stroke="#fff" stroke-width="1.1"/></svg>
      </div>
    </div>
  </div>
</body>
</html>
```